Erotik Online Shop
Zielgruppe
Kunden des Online Shops, vorzugsweise schwule Männer wobei der Shop auch die hetero Ziegruppe bedienen bzw. befriedigen kann.
Aufgabenstellung
Für den Relounch unserers Online Shops benötigen wir mehrer Grafiken für die Startseite des Shops sowie eventuell einen Überabreitung unseres Logos.

```html
<!DOCTYPE html>
<html lang="de">
<head>
<meta charset="utf-8">
<title>Pluvo24 – Startseiten-Banner</title>
<link href="https://fonts.googleapis.com/css2?family=Bebas+Neue&display=swap" rel="stylesheet">
<style>
:root{
  --red:#c8141c;
  --black:#111;
  --white:#fff;
  --canvas:#fff;
  --border:#dcdcdc;
  --panel:#2a2a2a;
  --panel-dark:#1a1a1a;
  --green:#3fb82a;
}
*{margin:0;padding:0;box-sizing:border-box}
html,body{width:1200px;height:1200px;overflow:hidden;background:var(--canvas)}
body{position:relative;font-family:"Bebas Neue",Impact,sans-serif;color:var(--black)}
.abs{position:absolute}
.banner{position:absolute;left:45px;width:600px;height:312px;border:1px solid var(--border);border-radius:6px;overflow:hidden;background:var(--white)}
.photo{position:absolute}
.tag{position:absolute;background:var(--black);color:var(--white);line-height:1;white-space:nowrap;padding:4px 8px 0}
.red{color:var(--red)}
.line{position:absolute;white-space:nowrap;line-height:1}

/* banner 1 */
.b1{top:36px}
.b1 .photo{left:330px;top:0;width:270px;height:312px;background:linear-gradient(90deg,#f4f4f4 0%,#9a9a9a 35%,#7b7b7b 60%,#dcdcdc 100%)}
/* banner 2 */
.b2{top:372px}
.b2 .photo{left:45px;top:0;width:255px;height:312px;background:linear-gradient(180deg,#d88f6b 0%,#c9765a 55%,#2e4a8e 78%,#2a3f78 100%)}
/* banner 3 */
.b3{top:720px}
.b3 .photo{left:0;top:0;width:600px;height:312px;background:linear-gradient(90deg,#e6c2a6 0%,#cf9f80 30%,#f4e6dc 55%,#fff 70%)}

.logo{position:absolute;left:776px;top:140px;font-size:72px;color:var(--black);letter-spacing:1px;line-height:1}

/* safer shopping */
.safe{position:absolute;left:732px;top:393px;width:399px;height:249px;background:linear-gradient(90deg,#555 0%,var(--panel) 40%,var(--panel-dark) 100%);box-shadow:0 3px 6px rgba(0,0,0,.4)}
.safe .photo{left:0;top:0;width:150px;height:249px;background:linear-gradient(90deg,#8a8a8a,#3a3a3a 90%)}
.safe .head{position:absolute;right:18px;top:14px;color:#ddd;font-size:30px}
.safe .badge{position:absolute;left:111px;top:52px;background:var(--white);color:var(--red);font-size:46px;padding:4px 12px 0;line-height:1}
.safe ul{position:absolute;right:18px;top:112px;list-style:none;text-align:right;color:var(--white);font-size:21px;line-height:25px}
.safe li svg{vertical-align:-3px;margin-left:10px}

/* small tiles */
.tile{position:absolute;top:744px;background:linear-gradient(180deg,#333,#151515);box-shadow:0 2px 5px rgba(0,0,0,.4)}
.pay{left:717px;width:138px;height:261px}
.pay .title{position:absolute;left:0;right:0;top:6px;text-align:center;color:var(--white);font-size:22px;line-height:21px;letter-spacing:1px}
.pay .row{position:absolute;left:12px;display:flex;align-items:center;gap:8px;color:var(--white);font-size:14px;line-height:1}
.pay .card{width:52px;height:32px;background:#d9d9d9;border-radius:3px}
.news{left:871px;width:135px;height:171px;text-align:center}
.news .big{position:absolute;left:0;right:0;top:12px;font-size:50px;line-height:44px;color:var(--white)}
.news .free{position:absolute;left:0;right:0;top:108px;color:var(--white);font-size:16px;letter-spacing:2px}
.news .btn{position:absolute;left:16px;right:16px;top:132px;height:24px;background:var(--red);color:var(--white);font-size:15px;line-height:26px}
.partner{left:1024px;width:135px;height:261px;text-align:center}
.partner .head{position:absolute;left:0;right:0;top:0;height:63px;background:var(--red);color:var(--white);font-size:28px;line-height:27px;padding-top:5px}
.partner .photo{left:0;top:63px;width:135px;height:100px;background:linear-gradient(180deg,#6a6a6a,#2c2c2c)}
.partner .box{position:absolute;left:6px;right:6px;height:26px;border:2px solid var(--white);background:var(--black);color:var(--white);font-size:18px;line-height:25px}
.partner .money{position:absolute;left:6px;right:6px;top:232px;height:24px;background:var(--red);color:var(--white);font-size:18px;line-height:25px}
.band{position:absolute;left:0;top:1073px;width:1200px;height:127px;background:var(--black)}
</style>
</head>
<body>

<section class="banner b1">
  <div class="photo" role="img" aria-label="Schwarzweißfoto eines muskulösen Männeroberkörpers in weißen Boxershorts"></div>
  <div class="tag" style="left:36px;top:42px;font-size:54px"><span class="red">Hot</span> Toys</div>
  <div class="line" style="left:44px;top:108px;font-size:30px">for</div>
  <div class="tag" style="left:100px;top:96px;font-size:62px"><span class="red">Hot</span> Boys</div>
  <div class="line" style="left:252px;top:170px;font-size:17px">(and girls)</div>
  <div class="line" style="left:15px;top:272px;font-size:30px">Come and get them. <span class="red">Now!</span></div>
</section>

<section class="banner b2">
  <div class="photo" role="img" aria-label="Foto eines schwitzenden Mannes mit nacktem Oberkörper und blauer Sporthose"></div>
  <div class="line" style="left:255px;top:69px;font-size:19px">Hot stuff for your</div>
  <div class="tag" style="left:255px;top:90px;font-size:56px;color:var(--red);padding:4px 6px 0">Private</div>
  <div class="tag" style="left:255px;top:144px;font-size:56px;color:var(--red);padding:4px 6px 0">Workouts</div>
  <div class="line" style="left:212px;top:272px;font-size:28px">Alles andere ist nur <span class="red">Spielzeug!</span></div>
</section>

<section class="banner b3">
  <div class="photo" role="img" aria-label="Foto eines Mannes mit langen Haaren und zurückgelegtem Kopf"></div>
  <div class="tag" style="left:268px;top:74px;font-size:56px;padding:4px 6px 0">Do it</div>
  <div class="tag" style="left:348px;top:128px;font-size:58px;color:var(--red);padding:4px 6px 0">Yourself</div>
  <div class="line" style="left:412px;top:196px;font-size:20px">Selbst ist der Mann!</div>
  <div class="line" style="left:118px;top:266px;font-size:29px">Hol dir das Zeug für echte Handwerker</div>
</section>

<div class="logo">Pluvo24</div>

<section class="safe">
  <div class="photo" role="img" aria-label="Dunkles Foto eines Männeroberkörpers"></div>
  <div class="head">Bei uns nie ohne...</div>
  <div class="badge">Safer Shopping</div>
  <ul>
    <li>Geld-zurück Garantie<svg width="18" height="16" viewBox="0 0 18 16"><path d="M2 8l5 5L16 2" fill="none" stroke="var(--green)" stroke-width="3.5"/></svg></li>
    <li>Diskrete Verpackung<svg width="18" height="16" viewBox="0 0 18 16"><path d="M2 8l5 5L16 2" fill="none" stroke="var(--green)" stroke-width="3.5"/></svg></li>
    <li>Kein Mindestbestellwert<svg width="18" height="16" viewBox="0 0 18 16"><path d="M2 8l5 5L16 2" fill="none" stroke="var(--green)" stroke-width="3.5"/></svg></li>
    <li>Faire &amp; günstige Versandkosten<svg width="18" height="16" viewBox="0 0 18 16"><path d="M2 8l5 5L16 2" fill="none" stroke="var(--green)" stroke-width="3.5"/></svg></li>
    <li>Onlineshopping seit 1999!<svg width="18" height="16" viewBox="0 0 18 16"><path d="M2 8l5 5L16 2" fill="none" stroke="var(--green)" stroke-width="3.5"/></svg></li>
  </ul>
</section>

<section class="tile pay">
  <div class="title"><span class="red">100% sicher</span><br>zahlen mit:</div>
  <div class="row" style="top:62px"><span class="card"></span>Norva</div>
  <div class="row" style="top:110px"><span class="card"></span>Circlo</div>
  <div class="row" style="top:158px"><span class="card"></span>Direkt-<br>pay</div>
  <div class="row" style="top:206px"><span class="card"></span>Walleto</div>
</section>

<section class="tile news">
  <div class="big">News<br><span class="red">Letter</span></div>
  <div class="free">100% free</div>
  <div class="btn">Register now</div>
</section>

<section class="tile partner">
  <div class="head">Partner<br>Programm</div>
  <div class="photo" role="img" aria-label="Foto eines Männerkörpers in Graustufen"></div>
  <div class="box" style="top:150px">Unser Banner</div>
  <svg class="abs" style="left:58px;top:178px" width="20" height="14" viewBox="0 0 20 14"><path d="M0 0h20L10 14z" fill="var(--white)"/></svg>
  <div class="box" style="top:193px">Deine Homepage</div>
  <div class="money">$ Dein Geld $</div>
</section>

<div class="band"></div>

</body>
</html>
```